Jolly Paws Business Card Update

I have a business card which I love. I want to keep the same logo, colours, font and style. I want to upgrade the scripting and remove some elements and add others.
On the front side under Services - remove the existing wording and insert - Providing individual coaching strategies to create happy, healthy and social canine companions
Under Denise Carvell amend the current wording to read: Qualified in Dog Behavioural Training, Natural Animal Healthcare and Animal Health Science
On the reverse side to remove the web address.

```html
<!DOCTYPE html>
<html lang="en">
<head>
<meta charset="utf-8">
<title>Jolly Paws Business Card</title>
<link href="https://fonts.googleapis.com/css2?family=Open+Sans:ital,wght@0,400;0,700;1,400&family=Exo+2:wght@400;600&display=swap" rel="stylesheet">
<style>
  :root {
    --backdrop: #2a2a2a;
    --blue-deep: #27459a;
    --blue-mid: #1a68b8;
    --blue-light: #0a90cf;
    --red-dark: #6a1a1c;
    --red-bright: #cc1f26;
    --cream: #efe8d6;
    --ring-red: #b81e24;
    --white: #ffffff;
    --text-soft: #e9eef7;
    --navy: #1c2a55;
  }
  * { margin: 0; padding: 0; box-sizing: border-box; }
  html, body { width: 1200px; height: 1138px; overflow: hidden; background: var(--backdrop); }
  body { position: relative; font-family: "Open Sans", sans-serif; }

  .card {
    position: absolute;
    border-radius: 14px;
    overflow: hidden;
    background: linear-gradient(35deg, var(--blue-deep) 0%, var(--blue-mid) 50%, var(--blue-light) 100%);
  }
  .card--front { left: 274px; top: 186px; width: 623px; height: 376px; }
  .card--back  { left: 275px; top: 608px; width: 619px; height: 374px; }

  .band {
    position: absolute; left: 0; right: 0; bottom: 0;
    background: linear-gradient(90deg, var(--red-dark) 0%, var(--red-bright) 55%, var(--red-dark) 100%);
    color: var(--text-soft);
    text-align: center;
  }
  .card--front .band { height: 74px; padding-top: 18px; font-size: 16.5px; line-height: 22px; }
  .card--back .band { height: 52px; padding-top: 13px; font-family: Arial, Helvetica, sans-serif; font-size: 16.5px; }

  .mark-circle {
    position: absolute; border-radius: 50%;
    background: var(--cream);
    border: 7px solid var(--ring-red);
  }
  .card--front .mark-circle { left: 237px; top: 35px; width: 150px; height: 150px; }
  .card--back .mark-circle { left: 64px; top: 84px; width: 168px; height: 168px; }

  .brand-name {
    position: absolute; left: 0; right: 0; text-align: center;
    top: 199px; font-size: 40px; font-weight: 700; letter-spacing: 1px;
    color: var(--text-soft); text-transform: uppercase;
  }
  .tagline {
    position: absolute; left: 0; right: 0; text-align: center;
    top: 248px; font-size: 20px; color: var(--text-soft); letter-spacing: 0.3px;
  }
  .services-pill {
    position: absolute; left: 219px; top: 288px; width: 185px; height: 29px;
    border-radius: 15px; background: linear-gradient(180deg, #fafafa, #d9dde3);
    border: 2px solid var(--blue-mid);
    color: var(--navy); font-weight: 700; font-size: 17px; letter-spacing: 2.5px;
    text-align: center; line-height: 25px; z-index: 2;
  }

  .contact-block { position: absolute; left: 293px; top: 76px; color: var(--white); }
  .person-name { font-family: "Exo 2", sans-serif; font-weight: 600; font-size: 25px; line-height: 34px; }
  .qualifications { font-style: italic; font-size: 15.5px; line-height: 21.5px; color: var(--text-soft); margin-top: 2px; }
  .contact-list { list-style: none; margin-top: 20px; font-family: "Exo 2", sans-serif; font-size: 17px; }
  .contact-list li { display: flex; align-items: center; height: 23px; }
  .contact-list svg { width: 16px; height: 16px; margin-right: 20px; fill: var(--white); }
</style>
</head>
<body>

<section class="card card--front">
  <div class="mark-circle" role="img" aria-label="Brand emblem area: hands cradling a dog on a cream sunburst"></div>
  <div class="brand-name">Jolly Paws</div>
  <div class="tagline">HAPPY DOGS, HAPPY OWNERS</div>
  <div class="services-pill">SERVICES</div>
  <div class="band">
    Providing individual coaching strategies to create happy,<br>
    healthy and social canine companions
  </div>
</section>

<section class="card card--back">
  <div class="mark-circle" role="img" aria-label="Brand emblem area: hands cradling a dog on a cream sunburst"></div>
  <div class="contact-block">
    <div class="person-name">Denise Carvell</div>
    <p class="qualifications">Qualified in Dog Behavioural Training,<br>Natural Animal Healthcare and<br>Animal Health Science</p>
    <ul class="contact-list">
      <li><svg viewBox="0 0 16 16"><path d="M4 0h8a1 1 0 0 1 1 1v14a1 1 0 0 1-1 1H4a1 1 0 0 1-1-1V1a1 1 0 0 1 1-1zm1 2v8h6V2zm1 9v1h1v-1zm2 0v1h1v-1zm2 0v1h1v-1zM6 13v1h1v-1zm2 0v1h1v-1zm2 0v1h1v-1z"/></svg>0400 000 123</li>
      <li><svg viewBox="0 0 16 16"><path d="M0 3h16v1L8 9 0 4zm0 3l8 5 8-5v7H0z"/></svg>jollypaws1@mailbox.com</li>
    </ul>
  </div>
  <div class="band">Promoting communication and connection between dogs and their families</div>
</section>

</body>
</html>
```